TA BRAMLEY BUSINESS CARD DESIGN PROJECT

We need to utilize our logo that was expertly created on PixelHarbor and now need to match this with a business card design.

```html
<!DOCTYPE html>
<html lang="en">
<head>
<meta charset="utf-8">
<title>TA Bramley Business Card</title>
<link href="https://fonts.googleapis.com/css2?family=Montserrat:wght@400;500;700;800&display=swap" rel="stylesheet">
<style>
  :root {
    --stage: #3a3a3c;
    --card-black: #141415;
    --card-back: #111112;
    --brand-blue: #0b57ad;
    --accent-blue: #1f6cd0;
    --deep-line: #0a0a0b;
    --text-white: #ffffff;
    --text-soft: #e6e6e6;
    --mark-grey: #2c2c2e;
  }
  * { margin: 0; padding: 0; box-sizing: border-box; }
  html, body { width: 1200px; height: 689px; overflow: hidden; }
  body {
    background: var(--stage);
    font-family: "Montserrat", sans-serif;
    position: relative;
  }
  .card {
    position: absolute;
    width: 520px;
    height: 300px;
    border-radius: 18px;
    overflow: hidden;
    top: 194px;
  }
  .card-back { left: 50px; background: var(--card-back); }
  .card-front { left: 630px; background: var(--card-black); }

  .back-brand {
    position: absolute;
    inset: 0;
    display: flex;
    align-items: center;
    justify-content: center;
    font-weight: 800;
    font-size: 54px;
    letter-spacing: 6px;
    color: var(--mark-grey);
  }

  .front-art { position: absolute; inset: 0; }

  .front-brand {
    position: absolute;
    top: 30px;
    right: 34px;
    font-weight: 800;
    font-size: 28px;
    letter-spacing: 4px;
    color: var(--text-white);
  }

  .contact {
    position: absolute;
    left: 34px;
    top: 178px;
    color: var(--text-white);
  }
  .contact-name {
    font-weight: 700;
    font-size: 18px;
    line-height: 22px;
    letter-spacing: 0.5px;
    color: var(--accent-blue);
  }
  .contact-role {
    font-size: 14px;
    line-height: 18px;
    font-weight: 400;
    color: var(--text-soft);
  }
  .contact-list { list-style: none; margin-top: 10px; }
  .contact-list li {
    display: flex;
    align-items: center;
    gap: 9px;
    font-size: 13px;
    line-height: 19px;
    color: var(--text-soft);
  }
  .contact-icon { width: 11px; height: 11px; flex: none; display: block; }

  .address {
    position: absolute;
    right: 30px;
    top: 176px;
    text-align: right;
    font-size: 13px;
    line-height: 18px;
    color: var(--text-soft);
  }
</style>
</head>
<body>

  <section class="card card-back" aria-label="Card back">
    <div class="back-brand">TA BRAMLEY</div>
  </section>

  <section class="card card-front" aria-label="Card front">
    <svg class="front-art" viewBox="0 0 520 300" aria-hidden="true">
      <path d="M0,0 H520 V72 C440,122 300,98 180,118 C100,132 40,146 0,162 Z" fill="var(--brand-blue)"/>
      <path d="M520,64 C440,114 300,90 180,110 C100,124 40,138 0,154" fill="none" stroke="var(--deep-line)" stroke-width="3"/>
      <path d="M505,96 C440,118 340,116 250,126" fill="none" stroke="var(--deep-line)" stroke-width="2"/>
      <line x1="190" y1="194" x2="505" y2="112" stroke="var(--accent-blue)" stroke-width="1"/>
    </svg>

    <div class="front-brand">TA BRAMLEY</div>

    <div class="contact">
      <div class="contact-name">OWEN CALDER</div>
      <div class="contact-role">Managing Director</div>
      <ul class="contact-list">
        <li>
          <svg class="contact-icon" width="11" height="11" viewBox="0 0 12 12"><path d="M2 1 L4.5 1 L5 3.5 L3.8 4.6 C4.5 6 6 7.5 7.4 8.2 L8.5 7 L11 7.5 L11 10 C6 10.5 1.5 6 2 1 Z" fill="var(--accent-blue)"/></svg>
          123 456 789
        </li>
        <li>
          <svg class="contact-icon" width="11" height="11" viewBox="0 0 12 12"><rect x="0.5" y="2.5" width="11" height="7" fill="var(--accent-blue)"/><path d="M0.5 2.5 L6 6.5 L11.5 2.5" fill="none" stroke="var(--card-black)" stroke-width="1"/></svg>
          info@yourmail.com
        </li>
        <li>
          <svg class="contact-icon" width="11" height="11" viewBox="0 0 12 12"><circle cx="6" cy="6" r="5.5" fill="var(--accent-blue)"/></svg>
          www.yourwebsite.com
        </li>
      </ul>
    </div>

    <div class="address">
      418 Linden Ridge Rd<br>
      Ashford, GA 30198
    </div>
  </section>

</body>
</html>
```